Road Construction Company needs business cards

We would like a new business card designed for our business.

We're a road construction company based in Qld, Australia.

Can the business card please have the following information on it.

Name: Warren Halbeck
Position: General Manager
Phone: 0472 915 348
Email: Warren.halbeck@tovrin.com.au
Address: 87 Marrow Ave, Pendlebay, QLD, 4023
Website: www.tovrin.com.au

Visually we'd like the card to be professional and simple.

Attached is our logo.

Our website is www.tovrin.com.au

Target Market(s)

Men aged 25-60

Contact Information for Business Card

As listed in project description

Font styles to use
Serif

Requirements
Must have
• Large logo on back of card

```html
<!DOCTYPE html>
<html lang="en">
<head>
<meta charset="utf-8">
<title>Tovrin Business Card</title>
<link href="https://fonts.googleapis.com/css2?family=Mulish:wght@400;700;800&display=swap" rel="stylesheet">
<style>
  :root {
    --page-bg: #e4e4e4;
    --brand-navy: #0d4d9c;
    --brand-blue-deep: #0a4591;
    --brand-blue-light: #1668b3;
    --accent-line: #2f8fd0;
    --text-grey: #555a60;
    --card-white: #f2f2f2;
  }
  * { box-sizing: border-box; margin: 0; padding: 0; }
  html, body { width: 1200px; height: 1200px; overflow: hidden; }
  body {
    background: var(--page-bg);
    font-family: "Mulish", sans-serif;
    position: relative;
  }
  .card {
    position: absolute;
    left: 234px;
    width: 730px;
    height: 418px;
    overflow: hidden;
  }
  .card-front { top: 160px; }
  .card-back { top: 632px; background: var(--card-white); }

  .front-pattern {
    position: absolute;
    inset: 0;
    background: linear-gradient(115deg, var(--brand-blue-deep) 0%, #0e55a2 55%, var(--brand-blue-light) 100%);
  }
  .front-wordmark {
    position: absolute;
    left: 331px;
    top: 268px;
    width: 289px;
    text-align: center;
    color: #ffffff;
    font-weight: 800;
    font-size: 46px;
    letter-spacing: 3px;
    line-height: 1;
  }

  .back-wordmark {
    position: absolute;
    left: 68px;
    top: 66px;
    color: var(--brand-navy);
    font-weight: 800;
    font-size: 34px;
    letter-spacing: 2px;
    line-height: 1;
  }
  .person {
    position: absolute;
    right: 67px;
    top: 176px;
    text-align: right;
  }
  .person-name {
    color: var(--brand-navy);
    font-weight: 700;
    font-size: 31px;
    line-height: 1.1;
  }
  .person-role {
    color: var(--text-grey);
    font-size: 19px;
    margin-top: 4px;
  }
  .divider {
    position: absolute;
    left: 68px;
    right: 67px;
    top: 247px;
    height: 2px;
    background: var(--accent-line);
  }
  .contact-list {
    position: absolute;
    left: 68px;
    top: 266px;
    list-style: none;
  }
  .contact-item {
    display: flex;
    align-items: center;
    height: 28px;
    color: var(--text-grey);
    font-size: 20px;
  }
  .contact-icon {
    width: 16px;
    height: 16px;
    margin-right: 10px;
    flex: none;
  }
  .address {
    position: absolute;
    right: 67px;
    top: 294px;
    text-align: right;
    font-style: normal;
    color: var(--text-grey);
    font-size: 20px;
    line-height: 26px;
  }
</style>
</head>
<body>
  <section class="card card-front">
    <div class="front-pattern" role="img" aria-label="Rows of embossed upward chevron shapes over a blue gradient"></div>
    <div class="front-wordmark">TOVRIN</div>
  </section>

  <section class="card card-back">
    <div class="back-wordmark">TOVRIN</div>

    <div class="person">
      <h1 class="person-name">Warren Halbeck</h1>
      <p class="person-role">General Manager</p>
    </div>

    <div class="divider"></div>

    <ul class="contact-list">
      <li class="contact-item">
        <svg class="contact-icon" viewBox="0 0 16 16" aria-hidden="true"><path fill="#0d4d9c" d="M3.6 1.5l2.2 2.6-1.3 1.6c.9 2.1 2.5 3.7 4.6 4.6l1.6-1.3 2.6 2.2-1.2 2.3C6.8 13.3 2.7 9.2 1.3 2.7z"/></svg>
        0472 915 348
      </li>
      <li class="contact-item">
        <svg class="contact-icon" viewBox="0 0 16 16" aria-hidden="true"><rect x="1" y="3" width="14" height="10" fill="#0d4d9c"/><path d="M1.5 3.5L8 8.8l6.5-5.3" fill="none" stroke="#f2f2f2" stroke-width="1.4"/></svg>
        Warren.halbeck@tovrin.com.au
      </li>
      <li class="contact-item">
        <svg class="contact-icon" viewBox="0 0 16 16" aria-hidden="true"><circle cx="8" cy="8" r="7" fill="#0d4d9c"/><path d="M1 8h14M8 1v14M8 1c-3 3-3 11 0 14M8 1c3 3 3 11 0 14" fill="none" stroke="#f2f2f2" stroke-width="1"/></svg>
        www.tovrin.com.au
      </li>
    </ul>

    <address class="address">87 Marrow Ave,<br>Pendlebay, QLD, 4023</address>
  </section>
</body>
</html>
```